VORLAND COMPOSITES INC website in USA

VORLAND COMPOSITES INC incorporated and operated in USA needs a completely new design of website. This Wyoming based company is a importer and distributor of composites material to supply mainly to American and Canadian/Mexican customers. Our main products includes Carbon Fiber, Aramid Fiber, Glass Fiber, Basalt Fiber, High Silica Glass, Quartz Fiber, S-Glass, Alumina Fiber, Vacuum Auxiliary.

We are one stop composites solution provider for Automotive, Aerospace, Construction, Electrical and Machinery industries.

We are exclusive sales company in North America for BLORAN composites produced from China and their other Asia facilities.

Target Market(s)

USA and Canada

Industry/Entity Type

Composites materials

Coding

Coded - Design and coding required

Number of Pages Required

5+ page

Requirements
Nice to have
• Color theme to match our corporate logo VORLAND. VORLAND stands for Northgate Provisioning Trade Holdings

```html
<!DOCTYPE html>
<html lang="en">
<head>
<meta charset="utf-8">
<title>VORLAND COMPOSITES INC</title>
<link href="https://fonts.googleapis.com/css2?family=Montserrat:wght@500;700&family=Open+Sans:wght@400;600;700&display=swap" rel="stylesheet">
<style>
:root{
  --orange:#f5a31a;
  --orange-dark:#e08f0a;
  --ink:#2b2b2b;
  --charcoal:#3b3b3b;
  --charcoal-deep:#2e2e2e;
  --grey-text:#6b6b6b;
  --light:#f4f4f4;
  --line:#d9d9d9;
  --white:#ffffff;
}
*{box-sizing:border-box;margin:0;padding:0}
html,body{width:1200px;height:4559px;overflow:hidden}
body{position:relative;font-family:"Open Sans",Arial,sans-serif;color:var(--ink);background:var(--white)}
.section{position:absolute;left:0;width:1200px;overflow:hidden}
.abs{position:absolute}
.eyebrow{color:var(--orange);font-size:14px;letter-spacing:.5px;text-transform:uppercase;font-weight:600}
.title{font-weight:600;font-size:31px}
.btn{position:absolute;background:var(--orange);color:var(--ink);font-weight:700;font-size:12px;text-transform:uppercase;display:flex;align-items:center;justify-content:center;border-radius:4px;letter-spacing:.3px}
.btn-ghost{background:transparent;border:2px solid var(--white);color:var(--white)}
.link{color:var(--orange);font-size:12px;font-weight:700;text-transform:uppercase}
.center{text-align:center;left:0;width:1200px}

/* hero */
.hero{top:0;height:640px;background:linear-gradient(180deg,#e9a64a 0%,#d9b07a 22%,#b9ab98 45%,#8f8f8f 75%,#6f6f6f 100%)}
.social{display:flex;gap:16px;left:80px;top:30px}
.social span{width:14px;height:14px;border-radius:50%;background:var(--ink);display:block}
.phone-top{right:82px;top:28px;font-size:11px;display:flex;align-items:center;gap:8px;color:var(--ink)}
.nav{top:62px;font-size:13px;font-weight:700;display:flex;align-items:center}
.nav a{color:var(--ink);text-decoration:none;padding:0 22px;border-right:1px solid rgba(0,0,0,.35);line-height:14px}
.nav a:last-child{border-right:0}
.nav .active{color:var(--white)}
.nav-left{left:60px}
.nav-right{left:735px}
.nav-rule{top:90px;height:1px;background:rgba(0,0,0,.3)}
.logo{left:525px;top:44px;display:flex;align-items:center;gap:8px}
.logo i{width:22px;height:22px;border-radius:50%;background:var(--orange);display:block}
.logo b{font-family:"Open Sans",sans-serif;font-weight:700;font-size:30px;color:var(--ink);letter-spacing:-.5px}
.hero h1{top:180px;font-family:"Montserrat",sans-serif;color:var(--white);font-size:49px;line-height:58px;font-weight:500}
.hero h1 strong{font-weight:700}
.hero p.lead{top:300px;color:var(--white);font-size:15px;line-height:23px}
.dots{left:578px;top:442px;display:flex;gap:7px}
.dots span{width:9px;height:9px;border-radius:50%;background:var(--white)}
.dots span.on{background:var(--orange)}

/* services */
.services{top:640px;height:615px;background:linear-gradient(180deg,#4a4a4a,#333 60%,#3a3a3a)}
.services .title,.articles .title{color:var(--white)}
.svc{width:320px;text-align:center;color:var(--white)}
.svc .ring{margin:0 auto;width:162px;height:162px;border-radius:50%;border:3px solid var(--white);display:flex;align-items:center;justify-content:center;position:relative}
.svc .ring .core{width:134px;height:134px;border-radius:50%;background:var(--charcoal-deep);border:5px solid var(--white);display:flex;align-items:center;justify-content:center}
.svc .num{position:absolute;left:8px;top:0;font-size:150px;line-height:160px;font-weight:700;color:transparent;-webkit-text-stroke:2px rgba(255,255,255,.8)}
.svc h3{font-size:18px;font-weight:600;margin-top:18px}
.svc p{font-size:11.5px;line-height:17px;color:#d5d5d5;margin:10px 18px 0}
.svc .link{display:block;margin-top:14px}
.next{width:26px;height:26px;border-radius:50%;border:1px solid #9a9a9a;display:flex;align-items:center;justify-content:center}

/* about */
.about{top:1255px;height:480px;background:var(--white)}
.about-photo{left:177px;top:70px;width:384px;height:380px;border-radius:50%;background:radial-gradient(circle at 60% 45%,#e9e6e2,#bfb6aa 60%,#8e7f6d)}
.about h2{font-size:31px;line-height:38px;font-weight:700}
.about p{font-size:12.5px;line-height:19px;color:var(--grey-text)}

/* products */
.products{top:1735px;height:680px;background:var(--white)}
.tabs{left:62px;top:147px;width:1067px;height:136px;display:flex;border:1px solid #bbb;border-bottom:0;border-radius:6px 6px 0 0;overflow:hidden;background:var(--light)}
.tab{flex:1;border-right:1px solid #bbb;display:flex;flex-direction:column;align-items:center;padding-top:10px;font-size:14px}
.tab:last-child{border-right:0}
.tab .thumb{width:86px;height:76px;background:linear-gradient(135deg,#9c9c9c,#5a5a5a);margin-bottom:8px}
.tab.on{background:var(--orange)}
.panel{left:62px;top:283px;width:1067px;height:363px;background:#2f2f2f;color:var(--white)}
.panel h3{font-size:22px;line-height:28px;font-weight:600}
.panel h3 em{color:var(--orange);font-style:normal}
.bullet{display:flex;gap:12px;font-size:10px;line-height:13px;color:#dcdcdc;width:410px}
.bullet::before{content:"";flex:none;width:8px;height:8px;border-radius:50%;background:var(--orange);margin-top:3px}
.bullet b{font-size:12px;color:var(--white);font-weight:600}
.panel-photo{left:538px;top:35px;width:506px;height:271px;border-radius:8px;background:linear-gradient(135deg,#5a5048,#8a7d70 45%,#b9aa96 70%,#6a5f55)}

/* catalogs */
.catalogs{top:2415px;height:656px;background:var(--white)}
.cat-photo{border-radius:50%;border:4px solid #8a5a1f;box-shadow:0 6px 14px rgba(0,0,0,.2)}
.cat-badge{width:112px;height:112px;border-radius:50%;background:var(--white);box-shadow:0 4px 10px rgba(0,0,0,.25);display:flex;align-items:center;justify-content:center}
.cat-badge span{width:92px;height:92px;border-radius:50%;background:var(--charcoal);display:flex;align-items:center;justify-content:center}
.cat-label{font-size:19px;line-height:30px;text-align:center;width:320px}

/* articles */
.articles{top:3071px;height:690px;background:linear-gradient(180deg,#3e3e3e,#333)}
.card{left:58px;top:154px;width:590px;height:395px;background:var(--white);border-radius:6px;overflow:hidden}
.card-photo{width:590px;height:227px;background:linear-gradient(135deg,#2c5f8c,#7aa6c8 50%,#dfe7ee)}
.date{font-size:12px;display:flex;gap:8px;align-items:center}
.date::before{content:"";width:12px;height:12px;background:var(--orange);border-radius:2px}
.side-photo{width:202px;height:182px;background:linear-gradient(135deg,#7d6c5a,#b7a894 60%,#4e4a46)}
.side-text{left:906px;width:235px;color:var(--white)}
.side-text h4{font-size:15px;line-height:19px;font-weight:600;margin:10px 0 8px}
.side-text p{font-size:10.5px;line-height:13px;color:#cfcfcf}
.side-text .link{display:block;margin-top:16px;font-size:11px}

/* contact */
.contact{top:3761px;height:480px;background:linear-gradient(180deg,#ffffff 0%,#ffffff 30%,#d9d9d9 68%,#3a3a3a 68%,#303030 100%)}
.contact-card{left:202px;top:62px;width:796px;height:384px;background:var(--light);display:flex}
.contact-photo{width:379px;height:384px;background:linear-gradient(135deg,#5c5c5c,#2a2a2a 60%,#161616)}
.form{position:relative;flex:1}
.form h2{position:absolute;left:0;width:100%;text-align:center;top:40px;font-size:38px;font-weight:400}
.field{position:absolute;left:72px;width:315px;height:28px;border:1px solid #b7b7b7;border-radius:5px;background:var(--white);font-size:11px;color:#9a9a9a;padding:6px 22px}

/* footer */
.footer{top:4241px;height:318px;background:#2f2f2f;color:var(--white)}
.footer h5{font-size:15px;font-weight:600}
.footer ul{list-style:none;font-size:10.5px;line-height:25px;color:#e5e5e5}
.fcontact li{display:flex;gap:10px;align-items:flex-start;line-height:14px;margin-bottom:25px}
.finput{background:#ececec;border-radius:3px;font-size:10px;color:#8a8a8a;padding:3px 8px;width:190px}
.bottom{left:0;top:290px;width:1200px;height:28px;background:#1f1f1f;font-size:10px;font-weight:700;display:flex;align-items:center;justify-content:center}
</style>
</head>
<body>

<header class="section hero">
  <div class="abs" style="inset:0" role="img" aria-label="Photo of an industrial city skyline in warm morning haze"></div>
  <div class="abs social" aria-label="Social links"><span></span><span></span><span></span><span></span></div>
  <div class="abs phone-top">
    <svg width="13" height="13" viewBox="0 0 24 24"><path fill="#2b2b2b" d="M6.6 10.8a15.1 15.1 0 006.6 6.6l2.2-2.2c.3-.3.7-.4 1-.2 1.1.4 2.3.6 3.6.6.6 0 1 .4 1 1V20c0 .6-.4 1-1 1A17 17 0 013 4c0-.6.4-1 1-1h3.5c.6 0 1 .4 1 1 0 1.3.2 2.5.6 3.6.1.3 0 .7-.2 1z"/></svg>
    Call us now ! +1 307 555 0148
  </div>
  <nav class="abs nav nav-left"><a class="active" href="#">HOME</a><a href="#">SERVICES</a><a href="#">ABOUT US</a><a href="#">PRODUCTS</a></nav>
  <div class="abs nav-rule" style="left:80px;width:410px"></div>
  <div class="abs nav-rule" style="left:756px;width:365px"></div>
  <div class="abs logo"><i></i><b>VORLAND</b></div>
  <nav class="abs nav nav-right"><a href="#">E-CATALOGS</a><a href="#">ARTICLES</a><a href="#">CONTACT US</a></nav>
  <h1 class="abs center"><strong>High-Performance</strong> Fibers.<br><strong>Delivered</strong> Across <strong>North America</strong></h1>
  <p class="abs center lead">Importing and distributing high-performance carbon, aramid, glass, basalt, and specialty fibers<br>for automotive, aerospace, construction, electrical, and machinery industries</p>
  <div class="btn" style="left:404px;top:372px;width:176px;height:36px">REQUEST A QUOTE</div>
  <div class="btn btn-ghost" style="left:594px;top:372px;width:202px;height:36px">DOWNLOAD CATALOGUE</div>
  <div class="abs dots"><span></span><span class="on"></span><span></span></div>
</header>

<section class="section services">
  <div class="abs center eyebrow" style="top:64px">Services</div>
  <h2 class="abs center title" style="top:90px">Our Services</h2>
  <p class="abs center" style="top:135px;font-size:12px;line-height:16px;color:#d5d5d5">At VORLAND, we go beyond materials — we deliver complete composite solutions<br>designed to optimize performance, reliability, and supply efficiency.</p>

  <div class="abs svc" style="left:79px;top:190px">
    <div class="num">1</div>
    <div class="ring"><div class="core">
      <svg width="52" height="52" viewBox="0 0 52 52"><circle cx="26" cy="26" r="24" fill="var(--orange)"/><rect x="14" y="17" width="24" height="16" rx="6" fill="#fff"/><path d="M20 33l-3 6 8-6z" fill="#fff"/><circle cx="21" cy="25" r="2" fill="var(--orange)"/><circle cx="26" cy="25" r="2" fill="var(--orange)"/><circle cx="31" cy="25" r="2" fill="var(--orange)"/></svg>
    </div></div>
    <h3>Technical Support</h3>
    <p>Get expert guidance on fiber selection, resin compatibility, and application engineering to ensure the right material for your performance goals.</p>
    <span class="link">Learn More →</span>
  </div>
  <div class="abs next" style="left:390px;top:258px"><svg width="10" height="10" viewBox="0 0 10 10"><path d="M1 5h8M6 2l3 3-3 3" stroke="#9a9a9a" fill="none"/></svg></div>

  <div class="abs svc" style="left:440px;top:190px">
    <div class="num">2</div>
    <div class="ring"><div class="core">
      <svg width="60" height="44" viewBox="0 0 60 44"><rect x="4" y="6" width="32" height="26" rx="2" fill="var(--orange)"/><rect x="17" y="6" width="6" height="10" fill="#fff"/><path d="M36 14h12l8 10v8H36z" fill="#fff"/><circle cx="14" cy="36" r="5" fill="#fff"/><circle cx="46" cy="36" r="5" fill="#fff"/></svg>
    </div></div>
    <h3>Logistics</h3>
    <p>Count on fast, reliable North American delivery. Our strategic warehouses and partnerships ensure your materials arrive on time, every time.</p>
    <span class="link">Learn More →</span>
  </div>
  <div class="abs next" style="left:775px;top:258px"><svg width="10" height="10" viewBox="0 0 10 10"><path d="M1 5h8M6 2l3 3-3 3" stroke="#9a9a9a" fill="none"/></svg></div>

  <div class="abs svc" style="left:801px;top:190px">
    <div class="num">3</div>
    <div class="ring"><div class="core">
      <svg width="52" height="52" viewBox="0 0 52 52"><circle cx="24" cy="24" r="18" fill="none" stroke="#fff" stroke-width="3"/><ellipse cx="24" cy="24" rx="8" ry="18" fill="none" stroke="#fff" stroke-width="3"/><path d="M6 24h36" stroke="#fff" stroke-width="3"/><circle cx="36" cy="36" r="7" fill="none" stroke="var(--orange)" stroke-width="3"/><path d="M41 41l6 6" stroke="var(--orange)" stroke-width="4"/></svg>
    </div></div>
    <h3>Sourcing Solutions</h3>
    <p>Gain direct access to our global VORLAND manufacturing network for consistent quality, competitive pricing, and supply assurance.</p>
    <span class="link">Learn More →</span>
  </div>

  <div class="btn" style="left:459px;top:516px;width:283px;height:38px">Learn More About Our Services</div>
</section>

<section class="section about">
  <div class="abs about-photo" role="img" aria-label="Photo of a person working at a laptop beside rolls of composite fabric"></div>
  <div class="abs eyebrow" style="left:646px;top:110px">About Us</div>
  <h2 class="abs" style="left:646px;top:135px;width:500px">Reliable, High-Performance Materials for Your Projects</h2>
  <p class="abs" style="left:646px;top:215px;width:360px">VORLAND COMPOSITES INC is a Wyoming-based company committed to supplying North America with high-performance composite materials. As the exclusive sales partner for BLORAN composites in the USA and Canada, we provide unmatched access to premium fibers and advanced materials from Asia's leading manufacturers.</p>
  <div class="btn" style="left:646px;top:357px;width:218px;height:36px">Learn More About Us</div>
</section>

<section class="section products">
  <div class="abs eyebrow" style="left:63px;top:18px">Products</div>
  <h2 class="abs title" style="left:62px;top:40px;font-weight:700">Our Product Range</h2>
  <p class="abs" style="left:63px;top:84px;width:700px;font-size:12px;line-height:19px;color:var(--grey-text)">VORLAND COMPOSITES provides a comprehensive selection of advanced fibers and vacuum auxiliaries, engineered to meet the demanding requirements of automotive, aerospace, construction, electrical, and industrial applications.</p>
  <div class="abs tabs">
    <div class="tab on"><div class="thumb" role="img" aria-label="Carbon fiber fabric"></div>Carbon Fiber</div>
    <div class="tab"><div class="thumb" role="img" aria-label="Aramid fiber spools" style="background:linear-gradient(135deg,#f3e3a0,#c9a63a)"></div>Aramid Fiber</div>
    <div class="tab"><div class="thumb" role="img" aria-label="Glass fiber strands" style="background:linear-gradient(135deg,#c8c8c8,#777)"></div>Glass Fiber</div>
    <div class="tab"><div class="thumb" role="img" aria-label="Basalt fiber roll" style="background:linear-gradient(135deg,#b7a68d,#6c5c48)"></div>Basalt Fiber</div>
    <div class="tab"><div class="thumb" role="img" aria-label="Quartz fiber cloth" style="background:linear-gradient(135deg,#eeeeee,#b9b9b9)"></div>Quartz Fiber</div>
    <div class="tab"><div class="thumb" role="img" aria-label="Alumina fiber fabric" style="background:linear-gradient(135deg,#a9a9a9,#4d4d4d)"></div>Alumina Fiber</div>
    <div class="tab"><div class="thumb" role="img" aria-label="Vacuum auxiliary mesh" style="background:linear-gradient(135deg,#6a6a6a,#1f1f1f)"></div>Vacuum Auxiliary</div>
  </div>
  <div class="abs panel">
    <h3 class="abs" style="left:30px;top:28px;width:450px">Introduction to the characteristics and applications of <em>Carbon Fiber</em> products:</h3>
    <div class="abs" style="left:30px;top:96px;font-size:17px">High Tensil Strength</div>
    <div class="abs bullet" style="left:30px;top:133px"><div><b>High -Temperature Tolarence -</b> Carbon fiber retains its properties up to about 2,500° C in non-oxidizing environments, far surpassing many other fibers in terms of thermal stability.</div></div>
    <div class="abs bullet" style="left:30px;top:189px"><div><b>Low Weight -</b> The density of carbon fiber is around 1.5-2.0 g/cm³, significantly lighter than steel (7.85 g/cm³), contributing to its high strength-to-weight ratio.</div></div>
    <div class="abs bullet" style="left:30px;top:233px"><div><b>High Stifness -</b> Carbon fibers exhibit high modulus, i.e., stiffness, typically 200-700 GPa, which means they deform very little under load, ideal for aerospace, sports equipment, and automotive industries.</div></div>
    <div class="btn" style="left:30px;top:302px;width:143px;height:34px">Learn More</div>
    <div class="abs panel-photo" role="img" aria-label="Photo of a rolled sheet of woven carbon fiber fabric"></div>
  </div>
</section>

<section class="section catalogs">
  <div class="abs center eyebrow" style="top:26px">E-Catalogs</div>
  <h2 class="abs center title" style="top:50px">Download Our Catalogs</h2>

  <div class="abs cat-photo" style="left:141px;top:155px;width:266px;height:266px;background:radial-gradient(circle,#c9c9c9,#4b4b4b 70%)" role="img" aria-label="Photo of a turbine fan made of composite blades"></div>
  <div class="abs cat-badge" style="left:218px;top:353px"><span>
    <svg width="44" height="44" viewBox="0 0 44 44"><path d="M22 6l16 8-16 8-16-8z" fill="#fff"/><path d="M6 21l16 8 16-8M6 28l16 8 16-8" stroke="#fff" stroke-width="3" fill="none"/></svg></span></div>
  <div class="abs cat-label" style="left:114px;top:480px">BLORAN 2024 Catalogue</div>

  <div class="abs cat-photo" style="left:450px;top:108px;width:300px;height:300px;background:radial-gradient(circle,#e8e6e3,#a9a39b 70%)" role="img" aria-label="Photo of hands cutting composite fabric with scissors"></div>
  <div class="abs cat-badge" style="left:544px;top:353px"><span>
    <svg width="40" height="48" viewBox="0 0 40 48"><path d="M4 2h22l10 10v34H4z" fill="#fff"/><rect x="12" y="28" width="5" height="12" fill="#3b3b3b"/><rect x="20" y="22" width="5" height="18" fill="#3b3b3b"/></svg></span></div>
  <div class="abs cat-label" style="left:440px;top:480px">Product Datasheets</div>

  <div class="abs cat-photo" style="left:793px;top:155px;width:266px;height:266px;background:radial-gradient(circle,#f1ece6,#b88f6d 75%)" role="img" aria-label="Photo of a certificate being sealed with wax"></div>
  <div class="abs cat-badge" style="left:870px;top:353px"><span>
    <svg width="44" height="48" viewBox="0 0 44 48"><circle cx="22" cy="18" r="14" fill="none" stroke="#fff" stroke-width="3"/><path d="M15 18l5 5 9-9" stroke="#fff" stroke-width="3" fill="none"/><path d="M14 30l-4 14 6-3 4 5 2-12M30 30l4 14-6-3-4 5" fill="#fff"/></svg></span></div>
  <div class="abs cat-label" style="left:766px;top:480px">Compliance &amp;<br>Certification Documents</div>

  <div class="btn" style="left:516px;top:557px;width:168px;height:36px">Download Now</div>
</section>

<section class="section articles">
  <div class="abs center eyebrow" style="top:60px">Articles</div>
  <h2 class="abs center title" style="top:90px">Industry Insights &amp; Resources</h2>

  <article class="abs card">
    <div class="card-photo" role="img" aria-label="Photo of engineers using a VR headset in a composites lab"></div>
    <div class="abs date" style="left:30px;top:245px">October 1, 2025</div>
    <h3 class="abs" style="left:30px;top:268px;font-size:22px;font-weight:400">Latest Trends in Composites Technology</h3>
    <p class="abs" style="left:30px;top:305px;width:440px;font-size:11px;line-height:14px;color:var(--grey-text)">Learn about emerging fiber materials, innovative manufacturing methods, and performance improvements in composite applications.</p>
    <span class="abs link" style="left:30px;top:353px">Learn More →</span>
  </article>

  <div class="abs side-photo" style="left:674px;top:154px" role="img" aria-label="Photo of an engineer reviewing fiber spools in a factory"></div>
  <div class="abs side-text" style="top:172px">
    <div class="date">September 5, 2025</div>
    <h4>Tips for Selecting the Right Fibers for Your Project</h4>
    <p>A practical guide to choosing carbon, aramid, glass, and specialty fibers based on strength, temperature, and environmental requirements.</p>
    <span class="link">Learn More →</span>
  </div>

  <div class="abs side-photo" style="left:674px;top:365px;background:linear-gradient(135deg,#6d6d6d,#a9a9a9 50%,#4a4a4a)" role="img" aria-label="Photo of reinforcing mesh on a construction site"></div>
  <div class="abs side-text" style="top:383px">
    <div class="date">August 28, 2025</div>
    <h4>Construction Applications: Reinforcing Materials</h4>
    <p>Case studies showing basalt and glass fibers in structural reinforcement and seismic retrofitting projects.</p>
    <span class="link">Learn More →</span>
  </div>

  <div class="btn" style="left:529px;top:581px;width:187px;height:36px">Read More Articles</div>
</section>

<section class="section contact">
  <div class="abs contact-card">
    <div class="contact-photo" role="img" aria-label="Photo of a businessman in a suit holding a phone"></div>
    <div class="form">
      <h2>Get in Touch</h2>
      <div class="field" style="top:110px">Name</div>
      <div class="field" style="top:147px">Email</div>
      <div class="field" style="top:184px">Product of Interest</div>
      <div class="field" style="top:222px;height:80px">Message</div>
      <div class="btn" style="left:152px;top:323px;width:152px;height:34px">Submit Inquiry</div>
    </div>
  </div>
</section>

<footer class="section footer">
  <div class="abs logo" style="left:62px;top:50px"><i></i><b style="color:#fff">VORLAND</b></div>
  <p class="abs" style="left:62px;top:100px;width:240px;font-size:10px;line-height:13px;color:#e5e5e5">VORLAND COMPOSITES INC is a Wyoming-based importer and distributor of advanced fibers and composite materials across North America.</p>
  <div class="abs social" style="left:62px;top:160px"><span style="background:#fff"></span><span style="background:#fff"></span><span style="background:#fff"></span></div>

  <h5 class="abs" style="left:425px;top:42px">Main Links</h5>
  <ul class="abs" style="left:425px;top:68px"><li>Home</li><li>Services</li><li>About Us</li><li>Products</li><li>E-Catalogs</li><li>Articles</li><li>Contact Us</li></ul>

  <h5 class="abs" style="left:635px;top:42px">Contact Us</h5>
  <ul class="abs fcontact" style="left:635px;top:76px;width:240px">
    <li><svg width="10" height="12" viewBox="0 0 10 12"><path d="M5 0a4 4 0 014 4c0 3-4 8-4 8S1 7 1 4a4 4 0 014-4z" fill="#fff"/></svg><span>Suite 410, Halden Tower, 22 Crest Road,<br>Cheyenne, WY 82001</span></li>
    <li><svg width="10" height="10" viewBox="0 0 24 24"><path fill="#fff" d="M6.6 10.8a15.1 15.1 0 006.6 6.6l2.2-2.2c.3-.3.7-.4 1-.2 1.1.4 2.3.6 3.6.6.6 0 1 .4 1 1V20c0 .6-.4 1-1 1A17 17 0 013 4c0-.6.4-1 1-1h3.5c.6 0 1 .4 1 1 0 1.3.2 2.5.6 3.6.1.3 0 .7-.2 1z"/></svg><span>+1 307 555 0192</span></li>
    <li><svg width="11" height="8" viewBox="0 0 11 8"><rect width="11" height="8" fill="#fff"/><path d="M0 0l5.5 4L11 0" stroke="#2f2f2f" fill="none"/></svg><span>sales@bloran-materials.com</span></li>
    <li><svg width="10" height="10" viewBox="0 0 10 10"><circle cx="5" cy="5" r="4.5" fill="#fff"/></svg><span>www.bloran-materials.com</span></li>
  </ul>

  <h5 class="abs" style="left:933px;top:42px">Subscribe Newslatter</h5>
  <div class="abs finput" style="left:933px;top:76px;height:22px">Email</div>
  <div class="abs finput" style="left:933px;top:104px;height:60px">Message</div>
  <div class="btn" style="left:933px;top:186px;width:96px;height:22px;font-size:10px">Submit</div>

  <div class="abs bottom">© 2025 VORLAND COMPOSITES INC. All rights reserved.</div>
</footer>

</body>
</html>
```